Exciting opportunity to create logo and a label for our natural health brand.

About us

We are a customer centric health supplement brand who believes in natural medicine and high quality ingredients. We take a holistic approach to healthcare, with an eastern philosophy. We believe in being partners with our customers in their health care journey and are invested in their well being.

Our brand philosophy and values are attached (see Vorna philosophy.png). Our personality traits are:

- Natural
- Fresh
- Modern
- Balanced (in a holistic sense)

Task breakdown

1. Design a fresh feeling logo for us
- We want it to represent our values and high quality ingredients. We would like the quality of the product to be reflected in the branding and have a high end feel.
- Logo text must include Vorna Health Sciences
- We want the Vorna to be the focus of the logo (see uploaded image Vorna logo example.png)
The logo does not have to follow this layout, but we just want the Vorna to stand out. Feel free to use your creative license on this!

2. Create an attractive label to go on the supplement bottle
- The designs need to be eye catching, give a sense of high end ingredients and natural products and tie in with the logo to give a joined up feel.
- We are selling our products online and need them to really stand out from the competition.
- See examples of labels and packaging we like (1 -7 label design).

The initial label we would like you to design would be for our product Calm Drift. It is a product that assists in the management of Anxiety and stress. The label will appear on the bottle that holds the capsules for this supplement, see uploaded files (Example plain bottles.png). The bottles may be white as the picture shows or dark blue recyclable plastic or dark brown glass . We don't have the exact dimensions of the bottle yet, but I will follow up with these.

The label needs to include the following things:
1. The logo
2. The name of the product
3. The product is to help with the relief of Anxiety and Stress
4. Number of capsules the bottle contains
5. The back of the label should have
i) The ingredients
ii) Dosage
iii) Directions of use

Please use placeholder text where needed.

We look forward to seeing your design. Thank you.

```html
<!DOCTYPE html>
<html lang="en">
<head>
<meta charset="utf-8">
<title>Vorna Health Sciences – Calm Drift label</title>
<link rel="stylesheet" href="https://fonts.googleapis.com/css2?family=Bebas+Neue&family=Poppins:wght@300;400;500;600&family=Roboto+Condensed:wght@400;700&display=swap">
<style>
  :root{
    --page:#ffffff;
    --cream:#f2e9d9;
    --ink:#2a2623;
    --rose:#bd5b60;
    --rose-dark:#9e5a5a;
    --taupe:#b88f7d;
    --blush:#cdb2a3;
    --amber:#d68b56;
    --brown:#8f5a3a;
    --brown-dark:#7f4a34;
    --fda-box:#ecd0c6;
    --line:#bd5b60;
  }
  *{margin:0;padding:0;box-sizing:border-box}
  html,body{width:1200px;height:1128px;overflow:hidden;background:var(--page)}
  body{position:relative;font-family:"Roboto Condensed",sans-serif;color:var(--ink)}

  /* ---------- shared brand + type ---------- */
  .brand-name{font-family:"Poppins",sans-serif;font-weight:400;color:var(--ink);line-height:1;letter-spacing:.06em;text-transform:uppercase}
  .brand-sub{font-family:"Poppins",sans-serif;font-weight:400;color:var(--ink);letter-spacing:.12em;text-transform:uppercase}
  .leaf-art{position:absolute;border-radius:50% 10% 50% 10%;
    background:radial-gradient(ellipse at 60% 40%,rgba(255,255,255,.55),rgba(220,210,194,.35) 60%,rgba(220,210,194,0) 75%)}
  .product-name{font-family:"Bebas Neue",sans-serif;font-weight:400;color:var(--ink);line-height:1;letter-spacing:.01em;white-space:nowrap}
  .claim-band{font-family:"Poppins",sans-serif;font-weight:400;white-space:nowrap;letter-spacing:.06em}
  .relief{font-family:"Poppins",sans-serif;font-weight:400;color:var(--ink);text-transform:uppercase;letter-spacing:.1em}
  .relief strong{font-weight:600}
  .count-band{font-family:"Poppins",sans-serif;color:#fff;text-transform:uppercase;letter-spacing:.1em;white-space:nowrap}

  /* ---------- front label variants ---------- */
  .front-label{
    position:absolute;top:197px;width:248px;height:291px;
    background:linear-gradient(90deg,#dcd6c9 0%,#f1ece2 35%,#efe9df 70%,#d9d3c6 100%);
    overflow:hidden;
  }
  .front-label .brand{position:absolute;left:45px;top:30px}
  .front-label .brand-name{font-size:32px}
  .front-label .brand-sub{font-size:8px;margin-top:5px}
  .front-label .leaf-art{left:121px;top:27px;width:92px;height:106px}
  .front-label .product-name{position:absolute;left:45px;top:162px;font-size:40px}
  .front-label .claim-band{position:absolute;left:40px;top:207px;width:168px;height:17px;font-size:10px;padding-left:6px;line-height:17px}
  .front-label .relief{position:absolute;left:47px;top:233px;font-size:10.5px;line-height:16px}
  .front-label .count-band{position:absolute;left:0;right:0;top:276px;height:15px;font-size:8px;line-height:15px;padding-left:45px}

  .v-rose{left:55px}  .v-rose .count-band{background:var(--rose)}
  .v-rose .claim-band{background:linear-gradient(90deg,rgba(205,150,150,.2),rgba(189,91,96,.45) 40%,rgba(189,91,96,.45) 80%,rgba(205,150,150,.1));color:#f6dede}
  .v-amber{left:336px} .v-amber .count-band{background:var(--amber)}
  .v-amber .claim-band{background:linear-gradient(90deg,rgba(214,139,86,.15),rgba(214,139,86,.4) 40%,rgba(214,139,86,.35) 80%,rgba(214,139,86,.05));color:#f8e3d2}
  .v-taupe{left:618px} .v-taupe .count-band{background:var(--taupe)}
  .v-taupe .claim-band{background:linear-gradient(90deg,rgba(205,178,163,0),rgba(205,178,163,.35) 45%,rgba(205,178,163,0));color:#5a4a42}
  .v-brown{left:900px} .v-brown .count-band{background:var(--brown-dark)}
  .v-brown .claim-band{background:linear-gradient(90deg,rgba(205,178,163,.2),rgba(189,140,130,.4) 40%,rgba(189,140,130,.35) 80%,rgba(205,178,163,.05));color:#f6e4dc}

  /* ---------- full wrap label ---------- */
  .wrap-label{position:absolute;left:125px;top:696px;width:893px;height:359px;background:var(--cream)}
  .back-panel{position:absolute;left:12px;top:17px;width:192px;font-size:11px;line-height:13.2px}
  .back-panel p{margin-bottom:9px}
  .label-head{color:var(--rose);font-weight:700}
  .caution{border-top:1.5px solid var(--line);border-bottom:1.5px solid var(--line);
    color:var(--rose);text-transform:uppercase;padding:5px 0 5px 1px;margin-top:0;letter-spacing:.02em;width:202px}
  .fda-note{background:var(--fda-box);margin-top:6px;padding:3px 5px;width:198px}

  .wrap-label .brand{position:absolute;left:344px;top:40px}
  .wrap-label .brand-name{font-size:46px}
  .wrap-label .brand-sub{font-size:11px;margin-top:8px}
  .wrap-label .leaf-art{left:438px;top:25px;width:133px;height:140px}
  .wrap-label .product-name{position:absolute;left:343px;top:196px;font-size:50px}
  .wrap-label .claim-band{position:absolute;left:336px;top:254px;width:222px;height:20px;font-size:13px;line-height:20px;padding-left:10px;
    background:linear-gradient(90deg,rgba(205,150,150,.15),rgba(189,91,96,.4) 30%,rgba(189,91,96,.4) 85%,rgba(205,150,150,.1));color:#f6e0e0}
  .wrap-label .relief{position:absolute;left:346px;top:280px;font-size:14px;line-height:21px}

  .facts-box{position:absolute;left:686px;top:13px;width:188px;height:174px;border:2px solid var(--ink);background:#fff;
    text-align:center;font-weight:700;font-size:10.5px;padding-top:7px;letter-spacing:.02em}
  .info-block{position:absolute;left:686px;width:200px;font-size:10.5px;line-height:13px}
  .info-block b{font-weight:700}
  .ingredients{top:199px}
  .maker{top:237px}

  .wrap-band{position:absolute;left:11px;right:0;bottom:0;height:19px;background:var(--rose);color:#fff;font-size:10px;line-height:19px}
  .wrap-band span{position:absolute;top:0}
  .wrap-band .url-left{left:41px}
  .wrap-band .count{left:331px;font-family:"Poppins",sans-serif;letter-spacing:.12em;font-size:10px}
  .wrap-band .url-right{left:705px}

  /* ---------- palette ---------- */
  .palette{position:absolute;left:1038px;top:698px;width:85px;height:286px;background:var(--cream);padding:11px 0 0 15px}
  .swatch{width:54px;height:26px;margin-bottom:12px}
</style>
</head>
<body>

  <section class="front-label v-rose" aria-label="Front label, rose variant">
    <div class="brand"><div class="brand-name">Vorna</div><div class="brand-sub">Health Sciences</div></div>
    <div class="leaf-art" role="img" aria-label="Faint embossed leafy branch decoration"></div>
    <h2 class="product-name">CALM DRIFT</h2>
    <div class="claim-band">Vitamins · Minerals · Herbs</div>
    <div class="relief">Relief of<br><strong>Anxiety</strong> and <strong>Stress</strong></div>
    <div class="count-band">60 Capsules | Dietary Supplement</div>
  </section>

  <section class="front-label v-amber" aria-label="Front label, amber variant">
    <div class="brand"><div class="brand-name">Vorna</div><div class="brand-sub">Health Sciences</div></div>
    <div class="leaf-art" role="img" aria-label="Faint embossed leafy branch decoration"></div>
    <h2 class="product-name">CALM DRIFT</h2>
    <div class="claim-band">Vitamins · Minerals · Herbs</div>
    <div class="relief">Relief of<br><strong>Anxiety</strong> and <strong>Stress</strong></div>
    <div class="count-band">60 Capsules | Dietary Supplement</div>
  </section>

  <section class="front-label v-taupe" aria-label="Front label, taupe variant">
    <div class="brand"><div class="brand-name">Vorna</div><div class="brand-sub">Health Sciences</div></div>
    <div class="leaf-art" role="img" aria-label="Faint embossed leafy branch decoration"></div>
    <h2 class="product-name">CALM DRIFT</h2>
    <div class="claim-band">Vitamins · Minerals · Herbs</div>
    <div class="relief">Relief of<br><strong>Anxiety</strong> and <strong>Stress</strong></div>
    <div class="count-band">60 Capsules | Dietary Supplement</div>
  </section>

  <section class="front-label v-brown" aria-label="Front label, brown variant">
    <div class="brand"><div class="brand-name">Vorna</div><div class="brand-sub">Health Sciences</div></div>
    <div class="leaf-art" role="img" aria-label="Faint embossed leafy branch decoration"></div>
    <h2 class="product-name">CALM DRIFT</h2>
    <div class="claim-band">Vitamins · Minerals · Herbs</div>
    <div class="relief">Relief of<br><strong>Anxiety</strong> and <strong>Stress</strong></div>
    <div class="count-band">60 Capsules | Dietary Supplement</div>
  </section>

  <section class="wrap-label" aria-label="Full wrap-around label">
    <div class="back-panel">
      <p><span class="label-head">SUGGESTED USE:</span> As a dietary supplement, take one capsule twice daily, preferably with meals.</p>
      <p><span class="label-head">WARNING:</span> If you are pregnant or breastfeeding, do not use this product. If symptoms persist or worsen, or if new symptoms develop, discontinue use and consult a health care practitioner. If you are taking prescription medications, consult a health care practitioner prior to use. Consumption with alcohol, other drugs or natural health products with sedative properties is not recommend</p>
      <div class="caution">Keep out of reach of children.<br>Do not use if safety seal is<br>damaged or missing. Store ia a<br>cool, dry place.</div>
      <div class="fda-note">These products have not been evaluated by the FDA and are not intended to diagnose, treat, cure, or prevent any disease.</div>
    </div>

    <div class="brand"><div class="brand-name">Vorna</div><div class="brand-sub">Health Sciences</div></div>
    <div class="leaf-art" role="img" aria-label="Faint embossed leafy branch decoration"></div>
    <h1 class="product-name">CALM DRIFT</h1>
    <div class="claim-band">Vitamins · Minerals · Herbs</div>
    <div class="relief">Relief of<br><strong>Anxiety</strong> and <strong>Stress</strong></div>

    <div class="facts-box">SUPPLEMENT FACTS</div>
    <div class="info-block ingredients"><b>INGREDIENTS:</b> Lorem ipsum dolor sit amet, consectetuer adipiscing elit, sed diam</div>
    <div class="info-block maker"><b>MANUFACTIRE:</b><br>VORNA HEALTH SCIENCES</div>

    <div class="wrap-band">
      <span class="url-left">www.vornahealthsciences.com</span>
      <span class="count">60 CAPSULES | DIETARY SUPPLEMENT</span>
      <span class="url-right">www.vornahealthsciences.com</span>
    </div>
  </section>

  <aside class="palette" aria-label="Colour palette">
    <div class="swatch" style="background:var(--rose)"></div>
    <div class="swatch" style="background:var(--rose-dark)"></div>
    <div class="swatch" style="background:var(--taupe)"></div>
    <div class="swatch" style="background:var(--blush)"></div>
    <div class="swatch" style="background:var(--amber)"></div>
    <div class="swatch" style="background:var(--brown)"></div>
    <div class="swatch" style="background:var(--brown-dark)"></div>
  </aside>

</body>
</html>
```